Fitness Centre/Personal Trainer Business Card

We need a business card design for a company based in Singapore called 'Vigor Ledger'.

We are a team of Personal Trainers and we are planning to open our new training facility.

This design will also be printed/painted on the walls in our gym.

We are a new breed of personal trainers who take fitness seriously and holistically. We do not merely train our clients to be big and muscular.

We believe in wholeness. In our opinion, fitness should include: strength, speed, flexibility, mobility, stamina & agility. These are what we train for. Of course, nutrition/diet is key.

We use fitness tools such as kettlebells, QVL, Pylometric boxes, battling ropes, clubbells, medicine balls, bulgarian bags etc - functional and non-bulky tools.

I currently have a Facebook page 'Vigor Ledger SG' which shows a logo of a kettlebell. But my business focus has since changed.

Services provided:
- Kettlebell Sport Preparation
- Calisthenics Training
- Corrective Exercises
- Sports Strength & Conditioning
- 28 days Weight Loss Program
- Myofascial Rehab Therapy
- Sports/Thai Massage

Main colors for the design should be BLACK & YELLOW. We envision a design which is able to protray the holistic view we take on fitness. Also it should somewhat appeal to the ladies and not intimidate them.

Target Market(s)

People between 18-35 years old. Students and working class alike.

Industry/Entity Type

Training

Requirements
Must have
• Name: Marcus Obadiah Lim
Fitness Coach
Corrective Exercise Specialist
M: +65 9437 2065
E: marcus@sgvigorledger-example.com

Double-sided please.
Nice to have
• "What is your vigor ledger?"

```html
<!DOCTYPE html>
<html lang="en">
<head>
<meta charset="utf-8">
<title>Vigor Ledger – Business Cards</title>
<link rel="stylesheet" href="https://fonts.googleapis.com/css2?family=Open+Sans:wght@400;600;700;800&family=Source+Sans+3:wght@400;600;700&display=swap">
<style>
  :root {
    --backdrop: #d9d9d7;
    --card: #000000;
    --yellow: #f5e11a;
    --yellow-soft: #f0dc2a;
    --white: #ffffff;
    --grey-line: #7a7a7a;
    --photo-dark: #1a1a1a;
    --photo-mid: #5e5e5e;
  }
  * { box-sizing: border-box; margin: 0; padding: 0; }
  html, body { width: 1200px; height: 722px; overflow: hidden; }
  body {
    background: var(--backdrop);
    font-family: "Source Sans 3", "Myriad Pro", sans-serif;
    position: relative;
  }
  .card {
    position: absolute;
    width: 488px;
    height: 279px;
    background: var(--card);
    overflow: hidden;
    box-shadow: 0 3px 10px rgba(0,0,0,.35);
  }
  .card--front   { left: 95px;  top: 65px; }
  .card--photo   { left: 614px; top: 62px; }
  .card--list    { left: 97px;  top: 381px; }
  .card--columns { left: 611px; top: 377px; }

  /* brand name block */
  .brand {
    position: absolute;
    display: flex;
    align-items: center;
    gap: 10px;
    font-family: "Open Sans", sans-serif;
    font-weight: 800;
    color: var(--yellow);
    line-height: 1;
  }
  .brand__dot { border-radius: 50%; background: var(--yellow); flex: none; }

  /* front */
  .card--front .brand { left: 40px; top: 58px; font-size: 26px; }
  .card--front .brand__dot { width: 34px; height: 34px; }
  .person-photo {
    position: absolute; left: 300px; top: 72px; width: 180px; height: 140px;
    background: radial-gradient(ellipse at 50% 55%, #b07a52 0%, #6b4630 35%, #1c1410 68%, #000 85%);
  }
  .holder-name {
    position: absolute; left: 33px; top: 200px;
    font-family: "Open Sans", sans-serif; font-weight: 600; font-size: 18.5px;
    color: var(--yellow); text-transform: uppercase; letter-spacing: .2px;
  }
  .holder-title {
    position: absolute; left: 33px; top: 227px;
    font-size: 12.5px; color: var(--white);
  }
  .divider {
    position: absolute; left: 0; right: 0; top: 246px; height: 2px; background: var(--grey-line);
  }
  .contact-row {
    position: absolute; left: 33px; right: 12px; top: 256px;
    display: flex; justify-content: space-between; font-size: 10.6px; color: var(--white); white-space: nowrap;
  }
  .contact-row span { display: flex; align-items: center; gap: 4px; }
  .contact-row svg { width: 8px; height: 9px; fill: var(--white); }

  /* photo card */
  .gym-photo {
    position: absolute; left: 0; top: 0; width: 330px; height: 279px;
    background:
      radial-gradient(ellipse at 40% 70%, #6a6a6a 0%, #3a3a3a 35%, transparent 70%),
      linear-gradient(90deg, var(--photo-mid) 0%, var(--photo-dark) 70%, #000 100%);
  }
  .card--photo .brand {
    left: 110px; top: 52px; font-size: 18px; flex-direction: column; align-items: center; gap: 6px; text-align: center;
  }
  .card--photo .brand__dot { width: 26px; height: 26px; }
  .services-right {
    position: absolute; right: 14px; top: 38px; text-align: right;
  }
  .services-heading {
    font-family: "Open Sans", sans-serif; font-weight: 700; color: var(--white); font-size: 17.5px;
  }
  .services-right ul { list-style: none; margin-top: 17px; }
  .services-right li {
    font-family: "Source Sans 3", sans-serif; font-weight: 700; font-size: 14.8px;
    color: var(--yellow); line-height: 28px;
  }
  .tagline {
    font-family: "Open Sans", sans-serif; font-weight: 700; letter-spacing: 1.2px;
    text-transform: uppercase; white-space: nowrap;
  }
  .card--photo .tagline { position: absolute; left: 20px; top: 254px; font-size: 15px; color: var(--white); }

  ul.bullets li::before { content: "\2022"; margin-right: 4px; }

  /* list card */
  .card--list .brand {
    left: 45px; top: 70px; flex-direction: column; align-items: flex-start; gap: 8px; font-size: 38px;
  }
  .card--list .brand__dot { width: 40px; height: 40px; }
  .card--list .services-block { position: absolute; left: 253px; top: 27px; }
  .card--list .services-heading { color: var(--yellow); font-size: 17.5px; }
  .card--list ul { list-style: none; margin-top: 14px; }
  .card--list li { font-size: 15px; color: var(--white); line-height: 25.2px; letter-spacing: .2px; }
  .card--list .tagline { position: absolute; left: 0; right: 0; top: 247px; text-align: center; font-size: 15px; color: var(--yellow); }

  /* columns card */
  .faint-brand {
    position: absolute; left: 50%; top: 26px; transform: translateX(-50%);
    display: flex; flex-direction: column; align-items: center; gap: 10px;
    font-family: "Open Sans", sans-serif; font-weight: 800; font-size: 46px; line-height: 1;
    color: var(--yellow); opacity: .18; text-align: center;
  }
  .faint-brand .brand__dot { width: 70px; height: 70px; border-radius: 50%; background: var(--yellow); }
  .card--columns .services-heading { position: absolute; left: 0; right: 0; top: 62px; text-align: center; font-size: 18px; }
  .service-grid {
    position: absolute; left: 36px; top: 98px; right: 20px; list-style: none;
    display: grid; grid-template-columns: auto auto; column-gap: 8px; row-gap: 7px; justify-content: start;
  }
  .service-grid li { font-size: 16.5px; color: var(--yellow-soft); letter-spacing: .2px; line-height: 24px; white-space: nowrap; }
  .service-grid li.service-grid__last { grid-column: 1 / span 2; justify-self: center; }
  .card--columns .tagline { position: absolute; left: 0; right: 0; top: 232px; text-align: center; font-size: 15px; color: var(--white); }
</style>
</head>
<body>

<section class="card card--front" aria-label="Card front">
  <div class="brand"><span class="brand__dot"></span>Vigor Ledger</div>
  <div class="person-photo" role="img" aria-label="Photo of a woman in black sportswear doing a push-up, seen from above"></div>
  <p class="holder-name">Marcus Obadiah Lim</p>
  <p class="holder-title">Fitness Coach, Corrective Exercise Specialist</p>
  <div class="divider"></div>
  <div class="contact-row">
    <span><svg viewBox="0 0 9 14"><rect x="1" y="0" width="7" height="14" rx="1.5"/><rect x="2.3" y="2" width="4.4" height="8" fill="#000"/></svg>+65 9437 2065</span>
    <span><svg viewBox="0 0 12 9"><rect width="12" height="9"/><path d="M0 0l6 5 6-5" stroke="#000" fill="none"/></svg>marcus@sgvigorledger-example.com</span>
    <span><svg viewBox="0 0 10 10"><circle cx="5" cy="5" r="5"/><path d="M0 5h10M5 0v10" stroke="#000" stroke-width=".8"/></svg>www.sgvigorledger-example.com</span>
  </div>
</section>

<section class="card card--photo" aria-label="Card back, photo version">
  <div class="gym-photo" role="img" aria-label="Black and white photo of two hexagonal dumbbells on a gym floor"></div>
  <div class="brand"><span class="brand__dot"></span>Vigor<br>Ledger</div>
  <div class="services-right">
    <h2 class="services-heading">Services</h2>
    <ul class="bullets">
      <li>Sports Strength &amp; Conditioning</li>
      <li>Kettlebell Sport Preparation</li>
      <li>28 days Weight Loss Program</li>
      <li>Myofascial Rehab Therapy</li>
      <li>Calisthenics Training</li>
      <li>Corrective Exercises</li>
      <li>Sports/Thai Massage</li>
    </ul>
  </div>
  <p class="tagline">What is your vigor ledger ?</p>
</section>

<section class="card card--list" aria-label="Card back, list version">
  <div class="brand"><span class="brand__dot"></span>Vigor<br>Ledger</div>
  <div class="services-block">
    <h2 class="services-heading">Services</h2>
    <ul class="bullets">
      <li>Sports Strength &amp; Conditioning</li>
      <li>Kettlebell Sport Preparation</li>
      <li>28 days Weight Loss Program</li>
      <li>Myofascial Rehab Therapy</li>
      <li>Calisthenics Training</li>
      <li>Corrective Exercises</li>
      <li>Sports/Thai Massage</li>
    </ul>
  </div>
  <p class="tagline">What is your vigor ledger ?</p>
</section>

<section class="card card--columns" aria-label="Card back, two-column version">
  <div class="faint-brand" aria-hidden="true"><span class="brand__dot"></span>Vigor<br>Ledger</div>
  <h2 class="services-heading">Services</h2>
  <ul class="service-grid bullets">
    <li>Sports Strength &amp; Conditioning</li>
    <li>Sports/Thai Massage</li>
    <li>Kettlebell Sport Preparation</li>
    <li>Corrective Exercises</li>
    <li>28 days Weight Loss Program</li>
    <li>Calisthenics Training</li>
    <li class="service-grid__last">Myofascial Rehab Therapy</li>
  </ul>
  <p class="tagline">What is your vigor ledger ?</p>
</section>

</body>
</html>
```